Business Card Design for The Lending Nest Inc.

We need a business card design for our mortgage company: "The Lending Nest Inc."

Need to have Social Media Account on there as a possibility

```html
<!DOCTYPE html>
<html lang="en">
<head>
<meta charset="utf-8">
<title>The Lending Nest Inc. – Business Card</title>
<link rel="stylesheet" href="https://fonts.googleapis.com/css2?family=Open+Sans:wght@400;700&display=swap">
<style>
  :root {
    --page-bg: #e9e9eb;
    --card-white: #ffffff;
    --brand-blue: #1f5fb0;
    --text-blue: #2a52b8;
    --text-grey: #4a4a4f;
    --sky-top: #7fb0d6;
    --sky-mid: #c9d6de;
    --city-dark: #4a5668;
    --city-mid: #8795a6;
    --shadow: rgba(30, 35, 45, 0.25);
  }
  * { box-sizing: border-box; margin: 0; padding: 0; }
  html, body { width: 1200px; height: 800px; overflow: hidden; }
  body {
    background: var(--page-bg);
    font-family: "Open Sans", Arial, sans-serif;
    display: flex;
    align-items: center;
    justify-content: center;
    gap: 60px;
  }
  .card {
    position: relative;
    width: 525px;
    height: 300px;
    background: var(--card-white);
    box-shadow: 0 10px 28px var(--shadow);
    overflow: hidden;
  }
  .cityscape {
    position: absolute;
    background:
      linear-gradient(115deg, rgba(255,255,255,0) 40%, rgba(255,255,255,0.35) 55%, rgba(255,255,255,0) 70%),
      linear-gradient(180deg, var(--sky-top) 0%, var(--sky-mid) 38%, var(--city-mid) 62%, var(--city-dark) 100%);
  }
  /* Front */
  .card--front .cityscape { inset: 0; }
  .brand-tag {
    position: absolute;
    left: 40px;
    top: 78px;
    width: 440px;
    height: 86px;
    background: var(--card-white);
    clip-path: polygon(0 0, 95% 0, 100% 25%, 100% 100%, 5% 100%, 0 75%);
    display: flex;
    align-items: center;
    gap: 16px;
    padding-left: 30px;
  }
  .brand-dot {
    width: 50px;
    height: 50px;
    border-radius: 50%;
    border: 4px solid var(--brand-blue);
    flex-shrink: 0;
  }
  .brand-name {
    color: var(--brand-blue);
    font-weight: 700;
    font-size: 30px;
    line-height: 1;
    white-space: nowrap;
  }
  .web-band {
    position: absolute;
    left: 0;
    right: 0;
    bottom: 0;
    height: 96px;
    background: rgba(255,255,255,0.92);
    display: flex;
    align-items: center;
    justify-content: center;
  }
  .web-address {
    color: var(--text-grey);
    font-size: 19px;
    letter-spacing: 2px;
  }
  /* Back */
  .card--back .cityscape { left: 0; top: 0; bottom: 0; width: 160px; }
  .logo-box {
    position: absolute;
    left: 20px;
    top: 52px;
    width: 130px;
    height: 108px;
    background: var(--card-white);
    display: flex;
    flex-direction: column;
    align-items: center;
    justify-content: center;
    gap: 8px;
  }
  .logo-box .brand-dot { width: 38px; height: 38px; border-width: 3px; }
  .logo-box .brand-name { font-size: 12px; text-align: center; white-space: normal; line-height: 1.2; }
  .contact-list {
    position: absolute;
    left: 200px;
    top: 92px;
    list-style: none;
    color: var(--text-blue);
    font-size: 18px;
    line-height: 1.4;
    text-transform: uppercase;
  }
</style>
</head>
<body>
  <article class="card card--front">
    <div class="cityscape" role="img" aria-label="Soft-focus city skyline photograph"></div>
    <div class="brand-tag">
      <span class="brand-dot"></span>
      <span class="brand-name">The Lending Nest Inc.</span>
    </div>
    <div class="web-band">
      <span class="web-address">WWW.NESTLEND.COM</span>
    </div>
  </article>

  <article class="card card--back">
    <div class="cityscape" role="img" aria-label="Soft-focus city skyline photograph"></div>
    <div class="logo-box">
      <span class="brand-dot"></span>
      <span class="brand-name">The Lending Nest Inc.</span>
    </div>
    <ul class="contact-list">
      <li>Name: Jane Rowe</li>
      <li>Phone: +198765432</li>
      <li>E-mail: hello@nestlend.com</li>
      <li>Web: nestlend.com</li>
    </ul>
  </article>
</body>
</html>
```